Business Cards for new orthopaedic surgery practice

My husband and I are starting our own orthopaedic surgery practice. We are looking for a business card that is uniform, but one will have my name/title and the other will have his. You can just create one design with my name on it for now. But when I choose your design as the winning design I will ask that you add another copy with his name/title.

We are looking for classy, simple, elite all in one. We like dark blues/a little gold/yellow. Something that goes with our logo. We want our logo incorporated. Here is all the info you need:
Business name: RV Bone & Vitality Center
Location: 38517 North Willowmere Ave
Maple Harbor, FL 33980
Phone: 954-218-4063
Fax: 954-582-7341
Email: info@myrvbonecare.example

Names: Lydia Vance, M.D.
Board Certified Hand and Upper Extremity Surgeon

Ebo Dansu, M.D.
Board Certified Hip & Knee Replacement/General Orthopaedic Surgeon

Can decide what you want to put on the back. Maybe a slogan:
Grounded in Care. Centered on You

I am just going to upload our logo. The only thing is if we select you as the winning design, the location, and phone numbers may change. We will need your help to update that once fully solidified.

Industry/Entity Type

Medical

Contact Information for Business Card

Colors
0054AA
0677BA
7BADD7
CADEEF
E8F1F8
0094D4
00A9DD
6FCCEA
C7EBF8
E9F6FB

Requirements
Must have
• class, appeal,
Should not have
• We want to air on the side of masculine if we are looking at masculine vs. feminine feel. But we still want it classy, sophisticated, and something we will love

```html
<!DOCTYPE html>
<html lang="en">
<head>
<meta charset="utf-8">
<title>RV Bone &amp; Vitality Center — Business Card</title>
<link href="https://fonts.googleapis.com/css2?family=Montserrat:wght@400;500;600;700&display=swap" rel="stylesheet">
<style>
  :root {
    --page: #e9e9ec;
    --paper: #ffffff;
    --navy: #1c2a4e;
    --ink: #1d1d22;
    --gold: #c8a263;
  }
  * { margin: 0; padding: 0; box-sizing: border-box; }
  html, body { width: 1200px; height: 1108px; overflow: hidden; }
  body {
    background: var(--page);
    font-family: "Montserrat", sans-serif;
    position: relative;
  }
  .card { position: absolute; width: 776px; }
  .card-front { left: 219px; top: 50px; height: 473px; background: var(--paper); }
  .card-back { left: 217px; top: 568px; height: 456px; background: var(--navy); }

  .brand-mark {
    position: absolute;
    border-radius: 50%;
    border: 2px solid var(--gold);
    display: flex; align-items: center; justify-content: center;
    text-align: center;
    font-weight: 700;
    text-transform: uppercase;
  }
  .card-front .brand-mark {
    left: 138px; top: 130px; width: 200px; height: 200px;
    color: var(--navy); font-size: 19px; line-height: 1.25; letter-spacing: 1px;
  }
  .card-back .brand-mark {
    left: 228px; top: 71px; width: 320px; height: 320px;
    color: #ffffff; font-size: 31px; line-height: 1.25; letter-spacing: 2px;
  }

  .divider { position: absolute; left: 368px; top: 128px; width: 2px; height: 232px; background: var(--navy); }

  .details { position: absolute; left: 387px; top: 128px; }
  .doctor-name { font-size: 28px; font-weight: 700; color: var(--navy); line-height: 1.1; }
  .doctor-name .credential { color: var(--gold); }
  .doctor-title { margin-top: 6px; font-size: 18px; line-height: 22px; color: var(--ink); }
  .address { margin-top: 24px; font-size: 18px; line-height: 22px; color: var(--ink); }
  .contact-list { list-style: none; margin-top: 14px; }
  .contact-list li {
    display: flex; align-items: center; gap: 8px;
    font-size: 18px; line-height: 26.5px; color: var(--ink);
  }
  .contact-list svg { width: 15px; height: 15px; fill: var(--gold); flex: none; }

  .tagline-rule { position: absolute; left: 0; right: 0; top: 414px; height: 2px; background: var(--gold); }
  .tagline {
    position: absolute; left: 50%; top: 403px; transform: translateX(-50%);
    background: var(--paper); padding: 0 5px;
    font-size: 17.5px; font-weight: 700; color: var(--navy); white-space: nowrap;
  }
</style>
</head>
<body>
  <section class="card card-front">
    <div class="brand-mark">RV Bone &amp;<br>Vitality<br>Center</div>
    <div class="divider"></div>
    <div class="details">
      <h1 class="doctor-name">Lydia Vance, <span class="credential">M.D.</span></h1>
      <p class="doctor-title">Board Certified Hand and<br>Upper Extremity Surgeon</p>
      <p class="address">38517 North Willowmere Ave<br>Maple Harbor, FL 33980</p>
      <ul class="contact-list">
        <li>
          <svg viewBox="0 0 16 16" aria-hidden="true"><path d="M1 5c0-2 3-3 7-3s7 1 7 3v1h-4V4.6C10 4.2 9 4 8 4s-2 .2-3 .6V6H1z"/><path d="M3 7h10l1 7H2z"/></svg>
          954-218-4063
        </li>
        <li>
          <svg viewBox="0 0 16 16" aria-hidden="true"><path d="M4 1h8v4H4z"/><path d="M1 6h14v6h-3v-2H4v2H1z"/><path d="M5 11h6v4H5z"/></svg>
          954-582-7341
        </li>
        <li>
          <svg viewBox="0 0 16 16" aria-hidden="true"><path d="M1 3h14v1L8 9 1 4z"/><path d="M1 5.5l7 5 7-5V13H1z"/></svg>
          info@myrvbonecare.example
        </li>
      </ul>
    </div>
    <div class="tagline-rule"></div>
    <p class="tagline">Grounded in Care. Centered on You</p>
  </section>

  <section class="card card-back">
    <div class="brand-mark">RV Bone &amp;<br>Vitality<br>Center</div>
  </section>
</body>
</html>
```